GTP biz card

We need a business card design for our new company based in Los Angeles called "Gold Tide Pictures". We develop film and television projects. We work with investors, financiers, film production companies, film distribution and sales companies as well as studios. We would like to incorporate our logo (see attached) on a two-sided card. We need to include: name and title, address, phone, email and company website.

Target Market(s)

Business, financial and studio clients

Industry/Entity Type

Business

Contact Information for Business Card

Two-sided. We are thinking of the logo on one side and the information on the back. Please feel free to be creative! Thanks.

Requirements
Must have
• Please include the following text information, excluding the "CAPS CATEGORY:" and please allow the ability for us to change the name, title and email address for each company employee):
• NAME & TITLE:
• Neil Parker
• Managing Partner
• COMPANY NAME:
• GOLD TIDE PICTURES (please use existing logo)
• COMPANY ADDRESS:
• KTW Studio Park
• 2250 Halverd Street
• Harbor Wing, 4th Floor
• Manhattan Beach, CA 90412
• COMPANY PHONE NUMBER:
• 310-555-0148
• COMPANY WEBSITE ADDRESS:
• www.goldtidepicturesgroup.example
• EMAIL ADDRESS: (only one per card)
• peter@goldtidepicturesgroup.example
• bingo@goldtidepicturesgroup.example
• neil@goldtidepicturesgroup.example

```html
<!DOCTYPE html>
<html lang="en">
<head>
<meta charset="utf-8">
<title>Gold Tide Pictures – Business Card</title>
<link href="https://fonts.googleapis.com/css2?family=Lato:wght@400;700;900&display=swap" rel="stylesheet">
<style>
  :root {
    --backdrop: #2b2b2d;
    --card-black: #0b0c0e;
    --cyan: #2fb5d6;
    --cyan-light: #a9dfee;
    --text-light: #e6e9ec;
    --text-muted: #b9c2c8;
  }
  * { box-sizing: border-box; margin: 0; padding: 0; }
  html, body {
    width: 1200px; height: 900px; overflow: hidden;
    background: var(--backdrop);
    font-family: "Lato", Arial, sans-serif;
  }
  .canvas { position: relative; width: 1200px; height: 900px; }

  .card {
    position: absolute;
    width: 560px; height: 320px;
    border-radius: 22px;
    background: var(--card-black);
    overflow: hidden;
    box-shadow: 0 18px 40px rgba(0,0,0,.55);
  }
  .card-front { left: 60px; top: 70px; }
  .card-back  { left: 580px; top: 500px; }
  .card-shapes { position: absolute; inset: 0; }

  .brand { position: absolute; text-align: center; }
  .brand-mark {
    display: block; margin: 0 auto 14px;
    width: 84px; height: 84px; border-radius: 50%;
    background: radial-gradient(circle at 50% 50%, var(--cyan-light) 0%, var(--cyan) 35%, #0f4a5e 70%, rgba(11,12,14,0) 100%);
  }
  .brand-name {
    font-weight: 900; color: var(--cyan);
    font-size: 24px; letter-spacing: 2px; white-space: nowrap;
  }
  .brand-tagline {
    margin-top: 6px; font-weight: 700; color: var(--text-muted);
    font-size: 9px; letter-spacing: 2.6px; white-space: nowrap;
  }
  .card-front .brand { left: 0; right: 0; top: 78px; }

  .card-back .brand { left: 16px; width: 290px; top: 96px; }
  .card-back .brand-mark { width: 76px; height: 76px; margin-bottom: 12px; }
  .card-back .brand-name { font-size: 20px; }
  .card-back .brand-tagline { font-size: 8.5px; letter-spacing: 2.2px; }

  .holder {
    position: absolute; right: 24px; top: 10px; text-align: right;
  }
  .holder-name { font-weight: 900; font-size: 17px; color: #ffffff; letter-spacing: .5px; line-height: 1.1; }
  .holder-title { font-weight: 700; font-size: 10px; color: #eef8fb; letter-spacing: 1px; margin-top: 2px; }

  .contact { position: absolute; left: 330px; top: 86px; width: 215px; }
  .contact-address { font-weight: 700; font-size: 12.5px; color: var(--cyan); line-height: 1.35; margin-bottom: 12px; }
  .contact-line { display: flex; align-items: center; gap: 7px; font-size: 11px; color: var(--text-light); margin-bottom: 8px; white-space: nowrap; }
  .contact-line svg { flex: none; }
  .contact-web { font-weight: 900; font-size: 11px; color: var(--text-light); margin-top: 4px; white-space: nowrap; }
  .contact-web .domain { color: var(--cyan); }
</style>
</head>
<body>
<main class="canvas">

  <section class="card card-front" aria-label="Business card front">
    <svg class="card-shapes" width="560" height="320" viewBox="0 0 560 320">
      <defs>
        <linearGradient id="bandFront" x1="0" y1="0" x2="1" y2="0">
          <stop offset="0" stop-color="#2fb5d6"/>
          <stop offset=".55" stop-color="#a9dfee"/>
          <stop offset="1" stop-color="#2fb5d6"/>
        </linearGradient>
      </defs>
      <rect x="0" y="0" width="560" height="18" fill="url(#bandFront)"/>
      <rect x="0" y="302" width="560" height="18" fill="url(#bandFront)"/>
    </svg>
    <div class="brand">
      <span class="brand-mark"></span>
      <div class="brand-name">GOLD TIDE PICTURES</div>
      <div class="brand-tagline">A MEDIA ENTERTAINMENT COMPANY</div>
    </div>
  </section>

  <section class="card card-back" aria-label="Business card back">
    <svg class="card-shapes" width="560" height="320" viewBox="0 0 560 320">
      <defs>
        <linearGradient id="bandBack" x1="0" y1="0" x2="1" y2="0">
          <stop offset="0" stop-color="#2fb5d6"/>
          <stop offset=".55" stop-color="#3fbcdc"/>
          <stop offset="1" stop-color="#bfe6f1"/>
        </linearGradient>
        <linearGradient id="divider" x1="0" y1="0" x2="0" y2="1">
          <stop offset="0" stop-color="#cfe3ea" stop-opacity="0"/>
          <stop offset=".4" stop-color="#cfe3ea" stop-opacity=".8"/>
          <stop offset="1" stop-color="#cfe3ea" stop-opacity="0"/>
        </linearGradient>
      </defs>
      <rect x="0" y="0" width="560" height="56" fill="url(#bandBack)"/>
      <line x1="308" y1="80" x2="320" y2="300" stroke="url(#divider)" stroke-width="2"/>
    </svg>

    <div class="holder">
      <div class="holder-name">NEIL PARKER</div>
      <div class="holder-title">MANAGING PARTNER</div>
    </div>

    <div class="brand">
      <span class="brand-mark"></span>
      <div class="brand-name">GOLD TIDE PICTURES</div>
      <div class="brand-tagline">A MEDIA ENTERTAINMENT COMPANY</div>
    </div>

    <div class="contact">
      <div class="contact-address">KTW Studio Park<br>2250 Halverd Street<br>Harbor Wing, 4th Floor<br>Manhattan Beach, CA 90412</div>
      <div class="contact-line">
        <svg width="14" height="12" viewBox="0 0 14 12" aria-hidden="true"><path d="M1 4 Q7 -1 13 4 L11 6 L9 4 L5 4 L3 6 Z M3 7 H11 V11 H3 Z" fill="#e6e9ec"/></svg>
        <span>310-555-0148</span>
      </div>
      <div class="contact-line">
        <svg width="14" height="11" viewBox="0 0 14 11" aria-hidden="true"><rect x="1" y="1" width="12" height="9" fill="none" stroke="#e6e9ec" stroke-width="1.3"/><path d="M1 1 L7 6 L13 1" fill="none" stroke="#e6e9ec" stroke-width="1.3"/></svg>
        <span>neil@goldtidepicturesgroup.example</span>
      </div>
      <div class="contact-web">www.<span class="domain">goldtidepicturesgroup.example</span></div>
    </div>
  </section>

</main>
</body>
</html>
```